Vorelan.com Personal Trainer/Fitness Website

I want a website to market my personal training/Outdoor Bootcamp Class services, as well as to ditribute nutrivex. I need a logo as well I included an address for the Harbor Gales 1975 logo. I'd like Vorelan in place of Harbor Gales, and in Black and white, just different enough so I can't get sued by the PBL.
https://www.pictofind.example/imgres?imgurl=http%3A%2F%2Fwww.darnell-quibury.example%2Fwp-content%2Fuploads%2F2014%2F01%2Fgales_logo4.jpg&imgrefurl=http%3A%2F%2Fwww.darnell-quibury.example%2Fpbl-logo-redesigns-harbor-gales%2F&docid=_qkwzR7TBAgXpL&tbnid=m4tpU8KdOXjnRP%3A&w=600&h=450&client=ms-android-carrier&bih=512&biw=360&ved=0ahUKEwiRtpgyp9HMAhUTwGMKHRPMBWMQMwg6KBQwFA&iact=mrc&uact=8.
It should be about 5 pages 1. home 2. about 3. Services 4. Blog/Videos and programs 5. Contact.
http://www.dorvinfitness.example.uk/ is a website I like the style of.

Target Market(s)

Seattle area

Industry/Entity Type

Fitness

Coding

Coded - Design and coding required

Number of Pages Required

4 page

Font styles to use
Serif
Sans Serif

Requirements
Must have
• A minimal look
Nice to have
• A logo similar to the 1975 Harbor Galewinds Logo, with a Small Milo Brandt ripping his shirt open(with a picture of the logo on his shirt, picture within picture) to turn into Ironjaw in the center. Skyline is black, Background and small figure white(with black logo on shirt)

```html
<!DOCTYPE html>
<html lang="en">
<head>
<meta charset="utf-8">
<title>Vorelan — Personal Training &amp; Outdoor Bootcamp</title>
<link rel="stylesheet" href="https://fonts.googleapis.com/css2?family=Roboto:wght@400;500;700&family=Roboto+Condensed:wght@700&family=Lato:ital,wght@0,400;1,400&family=Open+Sans:wght@400&display=swap">
<style>
:root{
  --green:#0d6b3a;
  --green-soft:#2f8453;
  --red:#e8232a;
  --ink:#1b1b1b;
  --text:#333;
  --disc:#ececec;
  --footer:#000;
  --footer-box:#161616;
  --footer-line:#333;
}
*{box-sizing:border-box;margin:0;padding:0}
html,body{width:995px;height:1200px;overflow:hidden;background:#fff}
body{font-family:"Roboto",Arial,sans-serif;color:var(--text);position:relative}
.abs{position:absolute}

/* header */
.topbar{left:0;top:0;width:995px;height:3px;background:#000}
.header{left:0;top:3px;width:995px;height:100px;background:linear-gradient(#fff,#f1f1f1);border-bottom:1px solid #ddd;box-shadow:0 1px 3px rgba(0,0,0,.12)}
.brand{left:117px;top:42px;display:flex;align-items:center;gap:8px}
.brand-dot{width:30px;height:30px;border-radius:50%;background:var(--green);flex-shrink:0}
.brand-name{font:700 26px "Roboto",sans-serif;color:var(--green);letter-spacing:.5px}
.reserve{left:609px;top:24px;width:124px;height:28px;background:var(--green);color:#fff;font:500 12.5px/28px "Roboto",sans-serif;text-align:center;border-radius:2px}
.call{left:749px;top:23px;display:flex;gap:7px;align-items:center}
.call-label{font:400 12px "Roboto",sans-serif;color:var(--green)}
.call-number{font:400 16.5px "Roboto",sans-serif;color:var(--ink);line-height:1.1}
.nav{left:432px;top:78px;display:flex;align-items:center;height:18px}
.nav a{font:500 12px "Roboto",sans-serif;color:var(--ink);text-decoration:none;padding:0 16px;border-left:1px solid #999;line-height:15px}
.nav a:first-child{border-left:0;padding-left:0;padding-right:12px}
.nav a:last-child{padding-right:0}

/* hero */
.hero{left:0;top:103px;width:995px;height:369px;background:linear-gradient(180deg,#e9eef0 0%,#8fae5f 30%,#6f9740 55%,#9aae58 100%)}
.hero-title{left:120px;top:250px;font:700 24px/32px "Roboto",sans-serif;color:#fff;text-shadow:0 1px 4px rgba(0,0,0,.55);text-transform:uppercase}
.arrow{width:30px;height:30px;border-radius:50%;background:rgba(20,20,20,.85);display:flex;align-items:center;justify-content:center;top:261px}

/* services */
.section-title{left:0;top:500px;width:995px;text-align:center;font:700 21px "Roboto Condensed",sans-serif;color:var(--green)}
.title-rule{top:507px;height:12px;width:215px}
.service{width:186px;text-align:center;top:554px}
.service-ring{width:107px;height:107px;border-radius:50%;border:1px solid #ddd;margin:0 auto;display:flex;align-items:center;justify-content:center;background:#fff;box-shadow:0 10px 6px -8px rgba(0,0,0,.08)}
.service-disc{width:97px;height:97px;border-radius:50%;background:var(--disc);display:flex;align-items:center;justify-content:center}
.service-mark{width:56px;height:50px;border-radius:10px;background:radial-gradient(circle at 50% 45%,var(--green) 0%,var(--green) 55%,var(--green-soft) 100%)}
.service-name{margin-top:27px;font:700 14px/18.5px "Roboto",sans-serif;color:var(--green);text-transform:uppercase}
.divider{left:117px;top:749px;width:761px;height:1px;background:linear-gradient(90deg,transparent,#ddd 15%,#ddd 85%,transparent)}

/* columns */
.col-title{top:792px;font:700 16.5px "Roboto",sans-serif;color:var(--ink);text-transform:uppercase;padding-bottom:6px;border-bottom:1px dashed #bbb}
.col-title span{color:var(--green)}
.about-photo{left:117px;top:828px;width:224px;height:102px;background:linear-gradient(90deg,#f1c98f,#8a6d55 45%,#3a3330)}
.about-text{left:118px;top:939px;width:226px;font:400 10.5px/16.3px "Open Sans",sans-serif;color:var(--text);letter-spacing:.2px}
.more{top:1015px;font:400 10px "Roboto",sans-serif;color:var(--green);letter-spacing:.3px}
.avatar{left:382px;top:828px;width:72px;height:72px;border-radius:50%;border:3px solid var(--red);background:linear-gradient(#d9c7b4,#8d6d55)}
.reviewer{left:465px;top:850px;font:500 12px "Lato",sans-serif;color:var(--ink)}
.reviewer small{font:400 10.5px "Lato",sans-serif;color:#444}
.stars{left:465px;top:872px;display:flex;gap:6px}
.quote{left:381px;top:912px;width:229px;height:88px;border:1px solid #e3e3e3;border-radius:3px;padding:9px 8px 9px 10px;font:italic 11px/18.6px "Lato",sans-serif;color:#333}
.quote .mark{color:#bbb;font:700 16px Georgia,serif}
.field{left:653px;width:211px;height:23px;border:1px solid #bdbdbd;border-radius:2px;font:400 10px/21px "Open Sans",sans-serif;color:#555;padding-left:8px;box-shadow:inset 0 1px 2px rgba(0,0,0,.08);background:#fff}
.submit{left:653px;top:1012px;width:56px;height:19px;background:var(--red);color:#fff;font:700 11px/19px "Roboto",sans-serif;text-align:center;border-radius:2px}

/* footer */
.footer{left:0;top:1063px;width:995px;height:137px;background:var(--footer);border-top:2px solid #888}
.fbox{top:1087px;height:64px;background:var(--footer-box);border:1px solid var(--footer-line);padding:7px 10px}
.fbox h4{font:700 11.5px "Roboto",sans-serif;color:#fff;letter-spacing:.2px}
.news-input{position:absolute;left:8px;top:30px;width:150px;height:23px;background:#fff;font:400 11.5px/23px "Lato",sans-serif;color:#333;padding-left:7px;border-radius:1px}
.news-go{position:absolute;left:164px;top:30px;width:26px;height:23px;background:#fff;display:flex;align-items:center;justify-content:center}
.fcontact{font:400 10px/16px "Open Sans",sans-serif;color:#ddd;display:flex;align-items:center;gap:8px}
.fcontact svg{flex-shrink:0;width:10px}
.social{position:absolute;top:33px;width:20px;height:20px;border-radius:2px}
.fbrand{left:780px;top:1108px;display:flex;align-items:center;gap:7px}
.fbrand .brand-dot{width:22px;height:22px}
.fbrand .brand-name{font-size:19px}
.flinks{left:118px;top:1171px;font:400 10px "Roboto",sans-serif;color:#fff;letter-spacing:.2px}
.copyright{left:512px;top:1171px;font:400 10px "Roboto",sans-serif;color:#fff}
</style>
</head>
<body>

<div class="abs topbar"></div>
<header class="abs header"></header>
<div class="abs brand"><span class="brand-dot"></span><span class="brand-name">VORELAN</span></div>
<div class="abs reserve">RESERVE A SEAT</div>
<div class="abs call">
  <svg width="27" height="27" viewBox="0 0 27 27" aria-hidden="true"><circle cx="13.5" cy="13.5" r="12" fill="none" stroke="#e8232a" stroke-width="1.6"/><path d="M10 7c-2 1-2.5 3-1.5 6s3 6 5.5 7.5c1.5.8 3 .6 4-.6l-2.2-2.4-1.8 1c-1.4-1-2.8-3.2-3.3-5l1.7-1.2L11.4 7z" fill="#e8232a"/></svg>
  <div><div class="call-label">Call Us Today</div><div class="call-number">555 218 4470</div></div>
</div>
<nav class="abs nav">
  <a href="#"><svg width="14" height="12" viewBox="0 0 14 12" aria-label="Home"><path d="M7 0 0 6h2v6h4V8h2v4h4V6h2z" fill="#0d6b3a"/></svg></a>
  <a href="#">ABOUT</a><a href="#">SERVICES</a><a href="#">VIDEOS</a><a href="#">PROGRAMS</a><a href="#">CONTACT US</a>
</nav>

<section class="abs hero" role="img" aria-label="Outdoor training in a park: a man working battle ropes and a woman lifting a medicine ball"></section>
<h1 class="abs hero-title">Get fit and have fun<br>the way it should be</h1>
<div class="abs arrow" style="left:50px"><svg width="10" height="14" viewBox="0 0 10 14"><path d="M8 1 2 7l6 6" fill="none" stroke="#fff" stroke-width="1.5"/></svg></div>
<div class="abs arrow" style="left:913px"><svg width="10" height="14" viewBox="0 0 10 14"><path d="M2 1l6 6-6 6" fill="none" stroke="#fff" stroke-width="1.5"/></svg></div>

<h2 class="abs section-title">OUR SERVICES</h2>
<svg class="abs title-rule" style="left:197px" viewBox="0 0 215 12" aria-hidden="true"><path d="M0 1h208M20 5h190M60 9h155" stroke="#d2d2d2" stroke-width="1.3"/></svg>
<svg class="abs title-rule" style="left:588px" viewBox="0 0 215 12" aria-hidden="true"><path d="M7 1h208M5 5h190M0 9h155" stroke="#d2d2d2" stroke-width="1.3"/></svg>

<div class="abs service" style="left:125px"><div class="service-ring"><div class="service-disc"><div class="service-mark" role="img" aria-label="Pictogram of a trainer coaching a client"></div></div></div><div class="service-name">Personal<br>Training</div></div>
<div class="abs service" style="left:310px"><div class="service-ring"><div class="service-disc"><div class="service-mark" role="img" aria-label="Pictogram of a bootcamp group exercising"></div></div></div><div class="service-name">Outdoor Bootcamp<br>Classes</div></div>
<div class="abs service" style="left:497px"><div class="service-ring"><div class="service-disc"><div class="service-mark" role="img" aria-label="Pictogram of runners training together"></div></div></div><div class="service-name">Outdoor Group<br>Training</div></div>
<div class="abs service" style="left:682px"><div class="service-ring"><div class="service-disc"><div class="service-mark" role="img" aria-label="Pictogram of a client at a screen for online coaching"></div></div></div><div class="service-name">Online<br>Coaching</div></div>

<div class="abs divider"></div>

<h3 class="abs col-title" style="left:117px;width:226px">About <span>Vorelan</span></h3>
<div class="abs about-photo" role="img" aria-label="Woman running on a treadmill in a sunlit gym"></div>
<p class="abs about-text">Lorem ipsum dolor sit amet, consectetuer adipiscing elit, sed diam nonummy nibh euismod tincidunt ut laoreet dolore magna aliquam erat volutpat.</p>
<a class="abs more" style="left:272px">READ MORE »</a>

<h3 class="abs col-title" style="left:381px;width:230px">Client <span>Reviews</span></h3>
<div class="abs avatar" role="img" aria-label="Client portrait"></div>
<div class="abs reviewer">Reno K. on <small>March 20, 2016</small></div>
<div class="abs stars">
  <svg width="16" height="15" viewBox="0 0 16 15"><path d="M8 0l2.4 5 5.6.6-4.2 3.8 1.2 5.6L8 12.2 3 15l1.2-5.6L0 5.6 5.6 5z" fill="#b9b9b9"/></svg>
  <svg width="16" height="15" viewBox="0 0 16 15"><path d="M8 0l2.4 5 5.6.6-4.2 3.8 1.2 5.6L8 12.2 3 15l1.2-5.6L0 5.6 5.6 5z" fill="#b9b9b9"/></svg>
  <svg width="16" height="15" viewBox="0 0 16 15"><path d="M8 0l2.4 5 5.6.6-4.2 3.8 1.2 5.6L8 12.2 3 15l1.2-5.6L0 5.6 5.6 5z" fill="#b9b9b9"/></svg>
  <svg width="16" height="15" viewBox="0 0 16 15"><path d="M8 0l2.4 5 5.6.6-4.2 3.8 1.2 5.6L8 12.2 3 15l1.2-5.6L0 5.6 5.6 5z" fill="#b9b9b9"/></svg>
  <svg width="16" height="15" viewBox="0 0 16 15"><path d="M8 0l2.4 5 5.6.6-4.2 3.8 1.2 5.6L8 12.2 3 15l1.2-5.6L0 5.6 5.6 5z" fill="#555"/></svg>
</div>
<blockquote class="abs quote"><span class="mark">“</span> I have been training with Talbot for just a few weeks now and am already feeling a difference between this and past efforts to get healthy... <span class="mark">”</span></blockquote>
<a class="abs more" style="left:540px">READ MORE »</a>

<h3 class="abs col-title" style="left:653px;width:226px">Quick <span>Contact</span></h3>
<div class="abs field" style="top:829px">Name</div>
<div class="abs field" style="top:865px">Email</div>
<div class="abs field" style="top:901px">Phone</div>
<div class="abs field" style="top:936px;height:66px">Message</div>
<div class="abs submit">SUBMIT</div>

<footer class="abs footer"></footer>
<div class="abs fbox" style="left:117px;width:204px">
  <h4>SUBSCRIBE TO NEWSLETTER</h4>
  <div class="news-input">Email here</div>
  <div class="news-go"><svg width="9" height="12" viewBox="0 0 9 12"><path d="M2 1l5 5-5 5" fill="none" stroke="#0d6b3a" stroke-width="2.4"/></svg></div>
</div>
<div class="abs fbox" style="left:352px;width:117px">
  <h4>CONTACT US</h4>
  <div class="fcontact" style="margin-top:5px"><svg width="10" height="10" viewBox="0 0 10 10"><path d="M2 0 0 1.5C0 6 4 10 8.5 10L10 8 7.5 6 6 7C4.5 6.3 3.7 5.5 3 4l1-1.5z" fill="#ccc"/></svg>555-304-9182</div>
  <div class="fcontact"><svg width="10" height="8" viewBox="0 0 10 8"><rect width="10" height="8" fill="#ccc"/><path d="M0 0l5 4 5-4" fill="none" stroke="#161616"/></svg>info@vorelan.com</div>
</div>
<div class="abs fbox" style="left:501px;width:137px">
  <h4>FOLLOW US</h4>
  <span class="social" style="left:12px;background:#3b5a98"></span>
  <span class="social" style="left:74px;background:#1a84bc"></span>
  <span class="social" style="left:105px;background:#d9432f"></span>
</div>
<div class="abs brand fbrand"><span class="brand-dot"></span><span class="brand-name">VORELAN</span></div>
<div class="abs flinks">HOME &nbsp;•&nbsp; ABOUT &nbsp;•&nbsp; SERVICES &nbsp;•&nbsp; VIDEOS &nbsp;•&nbsp; PROGRAMS &nbsp;•&nbsp; CONTACT US</div>
<div class="abs copyright">COPYRIGHT 2016 © VORELAN All Rights Reserved • Privacy Policy • Terms of Use</div>

</body>
</html>
```